Business Card Design Project

We are an incubator company that helps young entrepreneur to launch new ideas into the market. We will be targeting investors or likewise; Angels, young entrepreneurs and technopreneurs.

Our logo is being tasked by pixelhive to design, therefore there is no logo for now.
You can us Lanternfield Pte Ltd as the logo for the time being.

Please let us have some versions of modern and yet professional designs; for words, you can indicate e.g (address), (Title)

thanks

Target Market(s)

young entrepreneurs
angels, investors

Industry/Entity Type

Business

Colors
3176b5
ffffff

Requirements
Must have
• able to project out our name; Lanternfield
Should not have
• Nothing childish or cartoon

```html
<!DOCTYPE html>
<html lang="en">
<head>
<meta charset="utf-8">
<title>Lanternfield Pte Ltd — Business Card</title>
<link rel="stylesheet" href="https://fonts.googleapis.com/css2?family=Source+Sans+3:wght@400;500&display=swap">
<style>
  :root {
    --brand-blue: #1ea3dc;
    --paper: #ffffff;
    --ink: #333333;
    --rule: #2b2b2b;
  }
  * { margin: 0; padding: 0; box-sizing: border-box; }
  html, body {
    width: 1200px;
    height: 831px;
    overflow: hidden;
    background: var(--paper);
  }
  .card {
    position: relative;
    width: 1200px;
    height: 831px;
    background: var(--paper);
    font-family: "Source Sans 3", "Myriad Pro", sans-serif;
    color: var(--ink);
    overflow: hidden;
  }
  .brand-panel {
    position: absolute;
    left: 0;
    top: 0;
    width: 469px;
    height: 831px;
    background: var(--brand-blue);
    overflow: hidden;
  }
  .brand-panel__disc {
    position: absolute;
    left: 0;
    top: 0;
  }
  .holder {
    position: absolute;
    left: 521px;
    top: 124px;
    line-height: 1;
  }
  .holder__name {
    font-size: 46px;
    font-weight: 400;
    letter-spacing: -0.5px;
  }
  .holder__title {
    margin-top: 3px;
    font-size: 33px;
    font-weight: 400;
  }
  .divider {
    position: absolute;
    left: 519px;
    width: 650px;
    height: 2px;
    background: var(--rule);
  }
  .divider--upper { top: 263px; }
  .divider--lower { top: 452px; }
  .company {
    position: absolute;
    left: 574px;
    top: 318px;
    line-height: 1;
  }
  .company__name {
    font-size: 50px;
    font-weight: 400;
    letter-spacing: -0.3px;
  }
  .company__address {
    margin-top: 8px;
    margin-left: -3px;
    font-size: 32px;
    font-weight: 400;
  }
  .contact {
    position: absolute;
    left: 521px;
    list-style: none;
    font-size: 36px;
    line-height: 1;
  }
  .contact--numbers { top: 521px; }
  .contact--online { top: 631px; }
  .contact__item {
    display: flex;
    align-items: center;
    height: 41px;
  }
  .contact__icon {
    width: 30px;
    height: 30px;
    margin-right: 28px;
    flex: none;
    fill: var(--ink);
  }
</style>
</head>
<body>
<main class="card">
  <div class="brand-panel">
    <svg class="brand-panel__disc" width="469" height="831" viewBox="0 0 469 831" role="img" aria-label="White disc with a decorative circuit-line motif in the lower corner">
      <circle cx="106" cy="728" r="121" fill="#ffffff"/>
    </svg>
  </div>

  <section class="holder">
    <p class="holder__name">Your name</p>
    <p class="holder__title">your position</p>
  </section>

  <div class="divider divider--upper"></div>

  <section class="company">
    <p class="company__name">LANTERNFIELD PTE LTD</p>
    <p class="company__address">48 Harbourlight Road, Brookvale 20917</p>
  </section>

  <div class="divider divider--lower"></div>

  <ul class="contact contact--numbers">
    <li class="contact__item">
      <svg class="contact__icon" viewBox="0 0 30 30" aria-label="Telephone">
        <path d="M2 10c0-4 6-6 13-6s13 2 13 6v2h-6v-3c-2-1-5-1-7-1s-5 0-7 1v3H2z"/>
        <path d="M8 13h14l4 13H4z"/>
      </svg>
      <span>+ 000 - 4821 - 3067</span>
    </li>
    <li class="contact__item">
      <svg class="contact__icon" viewBox="0 0 30 30" aria-label="Fax">
        <rect x="7" y="3" width="16" height="7"/>
        <rect x="2" y="11" width="26" height="11" rx="2"/>
        <rect x="8" y="19" width="14" height="9" fill="#fff" stroke="#333" stroke-width="2"/>
      </svg>
      <span>+ 000 - 4821 - 3069</span>
    </li>
  </ul>

  <ul class="contact contact--online">
    <li class="contact__item">
      <svg class="contact__icon" viewBox="0 0 30 30" aria-label="Email">
        <rect x="2" y="6" width="26" height="19" fill="none" stroke="#333" stroke-width="2.4"/>
        <path d="M3 7l12 10 12-10" fill="none" stroke="#333" stroke-width="2.4"/>
      </svg>
      <span>admin@lanternfield.com</span>
    </li>
    <li class="contact__item">
      <svg class="contact__icon" viewBox="0 0 30 30" aria-label="Website">
        <rect x="2" y="4" width="26" height="18" fill="none" stroke="#333" stroke-width="2.6"/>
        <rect x="13" y="22" width="4" height="4"/>
        <rect x="8" y="26" width="14" height="2.4"/>
      </svg>
      <span>lanternfield.com</span>
    </li>
  </ul>
</main>
</body>
</html>
```